QuillVane needs a dashboard page designed

Redesign the dashboard shown in the provided images.

There are two images:
- dashboard.png
- dashboard-expanded.png

NOTE: The vocabulary navigation on the left will be a very long list of words 100s, so keep that in mind when you're designing both the vocab navigation and the expanded vocab popup.

In the dashboard.png picture, there needs to be a progress chart showing the word progress like the following: review 1(show it as completed) -> review 2(show the user they are here) -> review 3(unvisited) -> review 4(unvisited)

The do-not-design-this-page.png image is for your reference only. It is not to be designed. Use it to understand the overall look and feel of the website to help you create the best dashboard page possible.
Updates

Need extra days to review

Industry/Entity Type

Education English learning

Number of Pages Required

1 page

Requirements
Must have
• The main navigation and main header cannot change between pages. See the do-not-design page for the main navigateion and header.
Should not have
• Do not add a person profile. We will not have images of our users. Keep the icons in the main navigation as they are.

```html
<!DOCTYPE html>
<html lang="en">
<head>
<meta charset="utf-8">
<title>QuillVane – Vocabulary</title>
<link href="https://fonts.googleapis.com/css2?family=Urbanist:wght@400;500;600;700&display=swap" rel="stylesheet">
<style>
:root{
  --page:#17191d;
  --panel:#1d2024;
  --panel-2:#22262b;
  --muted:#6b7177;
  --text:#d5d9dc;
  --modal:#37424a;
  --modal-chip:#2b343b;
  --modal-text:#ffffff;
  --modal-word:#d2d8dc;
  --close:#4a565e;
  --gold:#c9a227;
  --green:#3fae5a;
  --scrim:rgba(0,0,0,.62);
}
*{box-sizing:border-box;margin:0;padding:0}
html,body{width:1200px;height:892px;overflow:hidden;background:#0b0c0e}
body{font-family:"Urbanist",sans-serif;position:relative;color:var(--text)}
.page{position:absolute;inset:0;background:var(--page)}
.header{position:absolute;left:19px;top:25px;width:1162px;height:41px;background:var(--panel);border-radius:20px}
.brand-menu{position:absolute;left:44px;top:36px;font-size:13px;font-weight:500;color:var(--text);letter-spacing:.2px}
.brand-menu::after{content:"";display:inline-block;margin-left:8px;border:4px solid transparent;border-top:4px solid var(--text);vertical-align:-1px}
.site-name{position:absolute;left:0;right:0;top:33px;text-align:center;font-size:18px;font-weight:700;color:var(--text);letter-spacing:.3px}
.top-icon{position:absolute;top:35px;width:20px;height:20px}
.sidebar{position:absolute;left:19px;top:76px;width:243px;height:793px;background:var(--panel);border-radius:18px}
.side-icon{position:absolute;left:34px;width:16px;height:16px}
.side-filter{position:absolute;left:91px;top:100px;font-size:11px;color:var(--text)}
.side-item{position:absolute;left:103px;font-size:8px;color:var(--muted)}
.status-card{position:absolute;left:297px;top:88px;width:856px;height:115px;background:var(--panel);border-radius:16px}
.status{position:absolute;left:1014px;font-size:10px;color:var(--muted)}
.word-head{position:absolute;right:71px;top:242px;font-size:15px;font-weight:600;color:var(--text)}
.word-desc{position:absolute;right:73px;font-size:10.5px;color:var(--muted)}
.chart-card{position:absolute;left:297px;top:375px;width:856px;height:362px;background:var(--panel);border-radius:16px}
.y-label{position:absolute;width:72px;text-align:right;left:300px;font-size:7.5px;line-height:15px;color:var(--muted)}
.x-label{position:absolute;top:679px;font-size:7.5px;color:var(--muted)}
.axis-title{position:absolute;left:681px;top:704px;font-size:10px;font-weight:600;color:var(--muted)}
.chart-svg{position:absolute;left:0;top:0}
.analysis-title{position:absolute;left:300px;top:773px;font-size:16.5px;font-weight:700;color:var(--text)}
.analysis-body{position:absolute;left:301px;top:809px;width:830px;font-size:11px;line-height:24.5px;color:var(--muted)}
.scrim{position:absolute;inset:0;background:var(--scrim)}
.vocab-modal{position:absolute;left:111px;top:118px;width:978px;height:364px;background:var(--modal);border-radius:25px}
.close-btn{position:absolute;left:1031px;top:132px;width:44px;height:44px;border-radius:50%;background:var(--close)}
.filter-chip{position:absolute;left:154px;top:152px;width:70px;height:37px;background:var(--modal-chip);border-radius:4px;font-size:13px;font-weight:500;color:var(--modal-text);padding:10px 0 0 12px}
.filter-chip::after{content:"";position:absolute;left:50px;top:17px;border:4px solid transparent;border-top:4px solid var(--modal-text)}
.group-title{position:absolute;left:185px;font-size:11.5px;font-weight:600;color:var(--modal-text);letter-spacing:.1px}
.group-icon{position:absolute;left:153px;width:16px;height:16px}
.word-list{position:absolute;left:185px;display:flex;gap:24px;font-size:10px;font-weight:500;color:var(--modal-word);letter-spacing:.2px}
</style>
</head>
<body>
<div class="page">
  <div class="header"></div>
  <div class="brand-menu">WORDNEST TUTOR</div>
  <div class="site-name">QUILLVANE</div>
  <svg class="top-icon" style="left:1043px" viewBox="0 0 20 20"><circle cx="10" cy="10" r="6" fill="none" stroke="#6b7177" stroke-width="3" stroke-dasharray="3 2"/><circle cx="10" cy="10" r="3" fill="#6b7177"/></svg>
  <svg class="top-icon" style="left:1086px" viewBox="0 0 20 20"><circle cx="10" cy="10" r="7" fill="none" stroke="#6b7177" stroke-width="1.6"/><path d="M6 10l3 3 7-8" fill="none" stroke="#6b7177" stroke-width="1.6"/></svg>
  <svg class="top-icon" style="left:1131px" viewBox="0 0 20 20"><circle cx="10" cy="7" r="3" fill="#6b7177"/><path d="M4 16c0-4 12-4 12 0z" fill="#6b7177"/></svg>

  <div class="sidebar"></div>
  <svg class="side-icon" style="top:111px" viewBox="0 0 16 16"><path d="M8 1L1 8h2v6h4v-4h2v4h4V8h2z" fill="#6b7177"/></svg>
  <svg class="side-icon" style="top:183px" viewBox="0 0 16 16"><circle cx="8" cy="5" r="3" fill="none" stroke="#6b7177" stroke-width="1.5"/><path d="M2 15c1-5 11-5 12 0z" fill="#6b7177"/></svg>
  <svg class="side-icon" style="top:254px" viewBox="0 0 16 16"><path d="M1 15V2h6v13zM9 15V7h6v8z" fill="#6b7177"/></svg>
  <div class="side-filter">ALL ▾</div>
  <div class="side-item" style="top:482px">GIVE IT A TRY</div>

  <div class="status-card"></div>
  <div class="status" style="top:110px"><span style="color:var(--green)">✓</span> COMPLETED</div>
  <div class="word-head">GRAB <span style="color:var(--gold);font-size:12px">★</span></div>
  <div class="word-desc" style="top:295px">to take something quickly, such as a coffee for</div>
  <div class="word-desc" style="top:319px">a short break, or to grab a bite to eat after</div>

  <div class="chart-card"></div>
  <div class="y-label" style="top:468px">LONG-TERM<br>MEMORY</div>
  <div class="y-label" style="top:515px">WORKING<br>MEMORY</div>
  <div class="y-label" style="top:571px">SHORT-TERM<br>MEMORY</div>
  <div class="y-label" style="top:626px">FORGOTTEN<br>MEMORY</div>
  <svg class="chart-svg" width="1200" height="892">
    <line x1="383" y1="664" x2="1120" y2="664" stroke="#2b3035"/>
    <g stroke="#6b7177" stroke-width=".7" stroke-dasharray="2 2" fill="none">
      <line x1="475" y1="581" x2="475" y2="664"/>
      <line x1="475" y1="581" x2="574" y2="664"/>
      <line x1="574" y1="489" x2="574" y2="664"/>
      <line x1="574" y1="489" x2="777" y2="664"/>
    </g>
    <circle cx="475" cy="581" r="2.5" fill="#6b7177"/>
    <circle cx="574" cy="489" r="2.5" fill="#6b7177"/>
    <text x="464" y="569" font-size="7.5" fill="#6b7177" font-family="Urbanist, sans-serif">18 MAY</text>
  </svg>
  <div class="x-label" style="left:384px">18 MAY</div>
  <div class="x-label" style="left:437px">12:00</div>
  <div class="x-label" style="left:484px">19 MAY</div>
  <div class="x-label" style="left:537px">12:00</div>
  <div class="x-label" style="left:583px">20 MAY</div>
  <div class="x-label" style="left:639px">12:00</div>
  <div class="x-label" style="left:685px">21 MAY</div>
  <div class="x-label" style="left:739px">12:00</div>
  <div class="x-label" style="left:785px">22 MAY</div>
  <div class="x-label" style="left:840px">12:00</div>
  <div class="x-label" style="left:886px">23 MAY</div>
  <div class="x-label" style="left:941px">12:00</div>
  <div class="x-label" style="left:987px">24 MAY</div>
  <div class="x-label" style="left:1042px">12:00</div>
  <div class="x-label" style="left:1089px">25 ...</div>
  <div class="axis-title">DATE RANGE</div>

  <div class="analysis-title">WORDNEST TUTOR LEARNING ANALYSIS</div>
  <p class="analysis-body">Lorem ipsum dolor sit amet, consectetur adipiscing elit. Nam rutrum commodo enim id bibendum. Nunc dignissim risus erat, nec finibus nunc dictum eu. Aliquam sit amet euismod metus, quis malesuada erat. Sed at felis quis nulla feugiat cursus at at dolor.</p>
</div>

<div class="scrim"></div>

<section class="vocab-modal" aria-label="Vocabulary list"></section>
<div class="close-btn">
  <svg width="44" height="44" viewBox="0 0 44 44"><path d="M15 15l14 14M29 15L15 29" stroke="#fff" stroke-width="2" stroke-linecap="round"/></svg>
</div>
<div class="filter-chip">ALL</div>

<svg class="group-icon" style="top:232px" viewBox="0 0 16 16"><circle cx="8" cy="9" r="5.5" fill="#fff"/><circle cx="8" cy="9" r="3.6" fill="var(--modal)"/><path d="M8 7v2.3l1.5 1" stroke="#fff" stroke-width="1.2" fill="none"/><circle cx="2.6" cy="3.2" r="1.8" fill="#fff"/><circle cx="13.4" cy="3.2" r="1.8" fill="#fff"/></svg>
<div class="group-title" style="top:233px">SHORT-TERM MEMORY</div>
<div class="word-list" style="top:266px"><span>GRAB</span></div>

<svg class="group-icon" style="top:313px" viewBox="0 0 16 16"><path d="M5.5 4V2.5h5V4" stroke="#fff" stroke-width="1.3" fill="none"/><rect x="1" y="4" width="14" height="4" rx="1" fill="#fff"/><rect x="1" y="9" width="14" height="5.5" rx="1" fill="#fff"/></svg>
<div class="group-title" style="top:314px">WORKING MEMORY</div>
<div class="word-list" style="top:350px">
  <span>COOL DOWN</span><span>CRAVE</span><span>GO FOR</span><span>GO-TO</span><span>IN THE MOOD FOR</span><span>SIP</span><span>SOOTHING</span><span>STICK WITH</span><span>THROW IN/THROW ON</span>
</div>

<svg class="group-icon" style="top:398px" viewBox="0 0 16 16"><path d="M4.5 7V5a3.5 3.5 0 017 0v2" stroke="#fff" stroke-width="1.6" fill="none"/><rect x="2.5" y="7" width="11" height="8" rx="1" fill="#fff"/></svg>
<div class="group-title" style="top:398px">LONG-TERM MEMORY</div>
<div class="word-list" style="top:434px"><span>GIVE IT A TRY</span></div>
</body>
</html>
```